Executive Business Card for Healthcare Company [Need Today]

I need a business card design for a healthcare company. The only branding the company has thus far is a logo. The cards will be utilized by company executives. The design I envision will be vibrant and appealing but with a corporate feel. They shouldn't be too casual or playful. I would like to complete this project TODAY if possible.

Target Market(s)

Healthcare vendors, other executives in healthcare and pharmaceuticals

Industry/Entity Type

Pharmaceutical

Contact Information for Business Card

See attachment

Font styles to use
Serif
Sans Serif

Colors

Designer to choose colors to be used in the design.

```html
<!DOCTYPE html>
<html lang="en">
<head>
<meta charset="UTF-8">
<title>Corvale Therapeutics – Executive Business Card</title>
<link href="https://fonts.googleapis.com/css2?family=Jost:wght@300;400&display=swap" rel="stylesheet">
<style>
  :root {
    --backdrop: #dfe2e1;
    --paper: #f4f4f1;
    --teal: #2ab5b8;
    --teal-deep: #1f9fa6;
    --ink: #4a4d4f;
    --ink-soft: #8a8e90;
    --white: #ffffff;
  }
  * { margin: 0; padding: 0; box-sizing: border-box; }
  html, body {
    width: 1200px; height: 900px; overflow: hidden;
    background: var(--backdrop);
    font-family: "Jost", "Futura", sans-serif;
  }
  .canvas {
    width: 1200px; height: 900px;
    display: flex; align-items: center; justify-content: center; gap: 56px;
  }
  .card {
    position: relative;
    width: 540px; height: 309px;
    border-radius: 3px;
    box-shadow: 0 6px 18px rgba(0,0,0,0.12);
  }
  .card--front { background: var(--paper); color: var(--ink); }
  .card--back {
    background: var(--teal);
    display: flex; align-items: center; justify-content: center;
  }

  /* brand lockup */
  .brand { display: flex; align-items: center; gap: 14px; }
  .brand__circle {
    border-radius: 50%; border: 2px solid currentColor; flex: none;
  }
  .brand__name { font-weight: 300; letter-spacing: 0.02em; }
  .card--front .brand {
    position: absolute; left: 34px; top: 30px; color: var(--teal-deep);
  }
  .card--front .brand__circle { width: 52px; height: 52px; }
  .card--front .brand__name { font-size: 24px; }
  .card--back .brand { color: var(--white); gap: 22px; }
  .card--back .brand__circle { width: 96px; height: 96px; border-width: 3px; }
  .card--back .brand__name { font-size: 36px; }

  .rule {
    position: absolute; height: 1px; background: var(--teal);
  }
  .rule--top { left: 34px; right: 34px; top: 112px; }
  .rule--mid { left: 250px; right: 34px; top: 208px; }

  .contact {
    position: absolute; left: 34px; top: 132px;
    list-style: none; font-size: 14px; line-height: 22px; color: var(--ink);
  }
  .contact li { display: flex; align-items: center; gap: 10px; }
  .contact svg { width: 11px; height: 11px; fill: none; stroke: var(--teal); stroke-width: 1.6; }

  .person {
    position: absolute; right: 34px; top: 160px; text-align: right;
  }
  .person__name { font-size: 22px; font-weight: 400; color: var(--teal-deep); line-height: 26px; }
  .person__title { font-size: 13px; color: var(--ink); line-height: 18px; }

  .address {
    position: absolute; right: 34px; top: 218px; text-align: right;
    font-size: 13.5px; line-height: 19px; color: var(--ink);
  }
  .address__company { color: var(--teal-deep); }
</style>
</head>
<body>
<main class="canvas">
  <section class="card card--front" aria-label="Business card front">
    <div class="brand">
      <span class="brand__circle"></span>
      <span class="brand__name">Corvale Therapeutics</span>
    </div>
    <div class="rule rule--top"></div>

    <ul class="contact">
      <li>
        <svg viewBox="0 0 12 12" aria-hidden="true"><path d="M2.5 1.5l2 2-1 1.2c.7 1.5 1.8 2.6 3.3 3.3l1.2-1 2 2-1.3 1.5C5.3 10.2 1.8 6.7 1.5 3.2z"/></svg>
        555-210-4478
      </li>
      <li>
        <svg viewBox="0 0 12 12" aria-hidden="true"><rect x="3" y="1" width="6" height="10" rx="1"/><path d="M5.5 9.2h1"/></svg>
        555-382-6190
      </li>
      <li>
        <svg viewBox="0 0 12 12" aria-hidden="true"><rect x="1" y="2.5" width="10" height="7"/><path d="M1 2.5l5 4 5-4"/></svg>
        dmoreau@corvalerx.com
      </li>
    </ul>

    <div class="person">
      <p class="person__name">Daniel Moreau</p>
      <p class="person__title">Senior Director of Marketing</p>
    </div>
    <div class="rule rule--mid"></div>
    <address class="address" style="font-style:normal">
      <span class="address__company">Corvale Therapeutics, LLC</span><br>
      118 Harlow Avenue<br>
      Fairhaven, GA 30999
    </address>
  </section>

  <section class="card card--back" aria-label="Business card back">
    <div class="brand">
      <span class="brand__circle"></span>
      <span class="brand__name">Corvale Therapeutics</span>
    </div>
  </section>
</main>
</body>
</html>
```